Note Cards for Clients

Hi - I need a design for simple flat note-cards and envelopes to use to send clients a written note in a professional manner. Please use my logo and color scheme.

Hi again- sorry for the miscommunication. I'd like to have note-cards 5x8 with envelopes as opposed to traditional stationary samples.

Thanks!

It Professional

```html
<!DOCTYPE html>
<html lang="en">
<head>
<meta charset="utf-8">
<title>Alder Bay Wealth Management – Stationery</title>
<link rel="stylesheet" href="https://fonts.googleapis.com/css2?family=Cinzel:wght@600&family=Montserrat:wght@400;500&display=swap">
<style>
  :root {
    --backdrop: #d3d3d4;
    --paper: #f4f4f4;
    --navy: #0c3577;
    --slate: #6a6a6a;
    --ink: #333840;
  }
  * { margin: 0; padding: 0; box-sizing: border-box; }
  html, body { width: 1200px; height: 922px; overflow: hidden; }
  body {
    background: var(--backdrop);
    position: relative;
    font-family: "Montserrat", Arial, sans-serif;
    color: var(--ink);
  }
  .sheet { position: absolute; background: var(--paper); overflow: hidden; }
  .letterhead { left: 143px; top: 168px; width: 421px; height: 595px; }
  .envelope-front { left: 614px; top: 92px; width: 441px; height: 220px; }
  .envelope-back { left: 615px; top: 362px; width: 440px; height: 221px; }
  .note-card { left: 615px; top: 632px; width: 422px; height: 198px; }

  .brand { position: absolute; display: flex; align-items: center; gap: 6px; color: var(--navy); }
  .brand-square { width: 30px; height: 30px; background: var(--navy); flex: none; }
  .brand-name {
    font-family: "Cinzel", Georgia, serif; font-weight: 600; color: var(--navy);
    line-height: 1.05;
  }
  .brand-name .line1 { display: block; font-size: 14.5px; letter-spacing: 0.2px; }
  .brand-name .line2 { display: block; font-size: 7.5px; letter-spacing: 0.8px; }

  .letterhead .brand { left: 27px; top: 24px; }
  .envelope-front .brand { left: 24px; top: 27px; }
  .note-card .brand { left: 24px; top: 24px; }

  .footer-line {
    position: absolute; left: 22px; right: 22px;
    display: flex; justify-content: space-between; align-items: center;
    font-size: 5.5px; color: var(--ink);
  }
  .letterhead .footer-line { bottom: 17px; }
  .envelope-front .footer-line { bottom: 16px; }
  .note-card .footer-line { bottom: 14px; }
  .contacts { display: flex; gap: 9px; }
  .contact { display: flex; align-items: center; gap: 3px; }
  .contact svg { width: 6px; height: 6px; }

  .edge-bands { position: absolute; left: 0; right: 0; bottom: 0; height: 7px; display: flex; gap: 3px; }
  .band-navy { background: var(--navy); flex: 0 0 41%; }
  .band-slate { background: var(--slate); flex: 1; }
  .envelope-front .band-navy { flex-basis: 41%; }
  .note-card .band-navy { flex-basis: 45%; }

  .flap { position: absolute; left: 0; top: 0; width: 440px; height: 63px; }
  .flap-mark { position: absolute; left: 210px; top: 20px; width: 20px; height: 20px; background: var(--paper); }
</style>
</head>
<body>

<section class="sheet letterhead" aria-label="Letterhead">
  <div class="brand">
    <span class="brand-square"></span>
    <span class="brand-name"><span class="line1">Alder Bay Wealth</span><span class="line2">Management, LLC</span></span>
  </div>
  <div class="footer-line">
    <span class="address">Level 12, Harbour House, 18 Quay Lane, Sydney</span>
    <span class="contacts">
      <span class="contact"><svg viewBox="0 0 6 6"><rect width="6" height="6" rx="1" fill="#0c3577"/><path d="M1.6 1.3h1l.3 1-.5.4a3 3 0 0 0 1 1l.4-.5 1 .3v1C3.2 4.6 1.4 2.8 1.6 1.3z" fill="#fff"/></svg>1300 555 017</span>
      <span class="contact"><svg viewBox="0 0 6 6"><rect width="6" height="6" rx="1" fill="#0c3577"/><rect x="1.2" y="1.8" width="3.6" height="2.4" fill="none" stroke="#fff" stroke-width=".5"/></svg>hello@alderbay.com</span>
      <span class="contact"><svg viewBox="0 0 6 6"><rect width="6" height="6" rx="1" fill="#0c3577"/><circle cx="3" cy="3" r="1.5" fill="none" stroke="#fff" stroke-width=".5"/></svg>www.alderbay.com</span>
    </span>
  </div>
  <div class="edge-bands"><span class="band-navy"></span><span class="band-slate"></span></div>
</section>

<section class="sheet envelope-front" aria-label="Envelope front">
  <div class="brand">
    <span class="brand-square"></span>
    <span class="brand-name"><span class="line1">Alder Bay Wealth</span><span class="line2">Management, LLC</span></span>
  </div>
  <div class="footer-line">
    <span class="address">Level 12, Harbour House, 18 Quay Lane, Sydney</span>
  </div>
  <div class="edge-bands"><span class="band-navy"></span><span class="band-slate"></span></div>
</section>

<section class="sheet envelope-back" aria-label="Envelope back">
  <svg class="flap" viewBox="0 0 440 63" preserveAspectRatio="none" aria-hidden="true">
    <polygon points="0,0 440,0 425,63 15,63" fill="#0c3577"/>
  </svg>
  <span class="flap-mark"></span>
</section>

<section class="sheet note-card" aria-label="Note card">
  <div class="brand">
    <span class="brand-square"></span>
    <span class="brand-name"><span class="line1">Alder Bay Wealth</span><span class="line2">Management, LLC</span></span>
  </div>
  <div class="footer-line">
    <span class="address">Level 12, Harbour House, 18 Quay Lane, Sydney</span>
    <span class="contacts">
      <span class="contact"><svg viewBox="0 0 6 6"><rect width="6" height="6" rx="1" fill="#0c3577"/><path d="M1.6 1.3h1l.3 1-.5.4a3 3 0 0 0 1 1l.4-.5 1 .3v1C3.2 4.6 1.4 2.8 1.6 1.3z" fill="#fff"/></svg>1300 555 017</span>
      <span class="contact"><svg viewBox="0 0 6 6"><rect width="6" height="6" rx="1" fill="#0c3577"/><rect x="1.2" y="1.8" width="3.6" height="2.4" fill="none" stroke="#fff" stroke-width=".5"/></svg>hello@alderbay.com</span>
      <span class="contact"><svg viewBox="0 0 6 6"><rect width="6" height="6" rx="1" fill="#0c3577"/><circle cx="3" cy="3" r="1.5" fill="none" stroke="#fff" stroke-width=".5"/></svg>www.alderbay.com</span>
    </span>
  </div>
  <div class="edge-bands"><span class="band-navy"></span><span class="band-slate"></span></div>
</section>

</body>
</html>
```